Card Design for my dog training business Brightpaw Obedience

Need a business card design for my dog training business with my new logo. Want the card to come off professional yet fun. Want it to be very eye catchy as well. I normally have these at vet clinics, pet stores, and groomers. so need it to look better than my competitors.
Target Market(s)
dog owners
Industry/Entity Type
Dog Training
Contact Information for Business Card
needs logo, my name and info
Font styles to use
Serif
Colors
0255a3
ffffff
ec1f27
000000
333333
fbfbfb
Requirements
Must have
- Brightpaw Obedience
- Felix Orland
- 415 903 2276
- info@brightpawobedience.example
- www.brightpawobedience.example

```html
<!DOCTYPE html>
<html lang="en">
<head>
<meta charset="utf-8">
<title>Brightpaw Obedience – Business Card</title>
<link rel="stylesheet" href="https://fonts.googleapis.com/css2?family=Noto+Serif:wght@400&family=EB+Garamond:ital@1&family=Open+Sans:wght@400&display=swap">
<style>
  :root {
    --brand-blue: #0255a3;
    --brand-red: #ec1f27;
    --ink-dark: #333333;
    --ink-black: #000000;
    --paper: #fbfbfb;
    --white: #ffffff;
    --backdrop: #e4e4e4;
    --panel-dark: #36383b;
  }
  * { margin: 0; padding: 0; box-sizing: border-box; }
  html, body { width: 1200px; height: 576px; overflow: hidden; }
  body { background: var(--backdrop); position: relative; }

  .card {
    position: absolute;
    top: 138px;
    width: 481px;
    height: 294px;
    background: var(--paper);
    border-radius: 12px;
    overflow: hidden;
    box-shadow: 0 1px 3px rgba(0,0,0,0.18);
  }
  .card--back { left: 82px; }
  .card--front { left: 602px; }

  .brand-mark {
    position: absolute;
    display: flex;
    flex-direction: column;
    align-items: center;
    gap: 10px;
    width: 200px;
  }
  .card--back .brand-mark { left: 140px; top: 62px; }
  .card--front .brand-mark { left: 18px; top: 62px; }
  .brand-mark__dot {
    width: 54px; height: 54px;
    border-radius: 50%;
    background: var(--ink-dark);
  }
  .brand-mark__name {
    font-family: "Noto Serif", serif;
    font-weight: 400;
    font-size: 19px;
    line-height: 1.2;
    color: var(--ink-dark);
    text-align: center;
  }

  .tagline {
    font-family: "EB Garamond", serif;
    font-style: italic;
    font-size: 12.5px;
    color: var(--white);
  }
  .tagline-band {
    position: absolute;
    left: 0; top: 254px;
    width: 100%; height: 30px;
    background: var(--brand-blue);
    display: flex; align-items: center; justify-content: center;
  }

  .wave { position: absolute; left: 0; top: 0; }

  .holder {
    position: absolute;
    right: 36px; top: 38px;
    text-align: right;
  }
  .holder__name {
    font-family: "Noto Serif", serif;
    font-size: 21px;
    color: var(--brand-blue);
    line-height: 1.2;
  }
  .holder__role {
    font-family: "Open Sans", sans-serif;
    font-size: 11.5px;
    color: var(--ink-dark);
    margin-top: 2px;
  }

  .contact-list {
    position: absolute;
    right: 20px; top: 195px;
    list-style: none;
  }
  .contact-list li {
    display: flex; align-items: center; justify-content: flex-end;
    gap: 8px;
    height: 19px;
    font-family: "Open Sans", sans-serif;
    font-size: 12px;
    color: var(--white);
  }
  .contact-list svg { width: 12px; height: 12px; }
  .card--front .tagline {
    position: absolute;
    right: 24px; top: 262px;
  }
</style>
</head>
<body>

  <section class="card card--back">
    <div class="brand-mark">
      <span class="brand-mark__dot"></span>
      <span class="brand-mark__name">Brightpaw Obedience</span>
    </div>
    <div class="tagline-band">
      <p class="tagline">“Training dogs across Texas one dog at a time.”</p>
    </div>
  </section>

  <section class="card card--front">
    <svg class="wave" width="481" height="294" viewBox="0 0 481 294">
      <path fill="var(--panel-dark)" d="M0,256 C120,264 220,236 300,200 C370,170 430,158 481,160 L481,294 L0,294 Z"/>
      <path fill="var(--brand-blue)" d="M40,226 C170,240 290,202 355,174 C405,152 450,144 481,144 L481,154 C440,154 400,166 350,188 C280,218 170,240 40,226 Z"/>
      <path fill="var(--brand-red)" d="M0,212 C70,230 150,236 240,224 C150,250 70,252 0,238 Z"/>
    </svg>

    <div class="brand-mark">
      <span class="brand-mark__dot"></span>
      <span class="brand-mark__name">Brightpaw Obedience</span>
    </div>

    <div class="holder">
      <h1 class="holder__name">Felix Orland</h1>
      <p class="holder__role">Dog Trainer</p>
    </div>

    <ul class="contact-list">
      <li>415 903 2276
        <svg viewBox="0 0 12 12" aria-hidden="true"><path fill="var(--white)" d="M1,4 C1,2 3,1 6,1 C9,1 11,2 11,4 L8.5,4.5 L8,3 L4,3 L3.5,4.5 Z M3,6 L9,6 L10,11 L2,11 Z"/></svg>
      </li>
      <li>info@brightpawobedience.example
        <svg viewBox="0 0 12 12" aria-hidden="true"><rect x="0.5" y="2.5" width="11" height="7.5" fill="var(--white)"/><path d="M0.5,2.5 L6,7 L11.5,2.5" fill="none" stroke="var(--panel-dark)" stroke-width="1"/></svg>
      </li>
      <li>www.brightpawobedience.example
        <svg viewBox="0 0 12 12" aria-hidden="true"><circle cx="6" cy="6" r="5.3" fill="var(--white)"/><path d="M0.8,6 H11.2 M6,0.7 V11.3 M6,0.7 C3,3 3,9 6,11.3 M6,0.7 C9,3 9,9 6,11.3" fill="none" stroke="var(--panel-dark)" stroke-width="0.8"/></svg>
      </li>
    </ul>
    <p class="tagline">“Training dogs across Texas one dog at a time.”</p>
  </section>

</body>
</html>
```